Cat-products company needs smart, yet endearing, business card

We need a business card design for a new, but up-and-running, business based in Honolulu, Hawaii. The business is Purrnest Nook Co. Our first product is the most environmentally-friendly cat grass kit ever seen on the planet. Future products, currently in the R&D phase, will include a variety of exciting cat scratchers. We also do consulting work to help apartment-dwellers make their home more cat-friendly and, in the future, plan on doing full, custom installs of structure to create high walkways for cats.

Target Market(s)

Middle-aged, apartment-dwelling, middle-class workers who own 1 or more cats and who dote on them.

Industry/Entity Type

Pet Care

Contact Information for Business Card

A striking, professional, yet warm and friendly design is what we're after.

Font styles to use
Serif
Sans Serif
Other font styles liked:
• Comfortaa

Colors

Designer to choose colors to be used in the design.

Requirements
Must have
• The company logo: (see attachment)
• The company name: Purrnest Nook Co
• The web address: www.purrnestnookco.com
• Email: support@purrnestnookco.com
• Phone: +1 (808) 571 6023
• Update (Fri Jun 30 3017 7:45pm Hawaii Time) I would like, is possible, uploaded picture of the cat grass kit on the back of the card with some text along the lines of: Purrnest Nook Co - Maker Of The Leafiest Feline Sprout Set Yet
Nice to have
• A cat picture, cartoon, real or silhouette that illustrates cats in action and/or relaxing; ie using the apartment space to live, play and relax in and being well-contented.
• Most of the website is done in the font: Comfortaa. It might be nice to continue using this for brand consistency.
Should not have
• Hard-to-read fonts.

```html
<!DOCTYPE html>
<html lang="en">
<head>
<meta charset="UTF-8">
<title>Purrnest Nook Co — Business Card</title>
<link rel="stylesheet" href="https://fonts.googleapis.com/css2?family=Jost:wght@400;500;700&display=swap">
<style>
  :root {
    --backdrop: #2b2b2d;
    --card-white: #ffffff;
    --cocoa: #5e3c33;
    --sun: #f6b01e;
    --ink: #3a2a26;
  }
  * { box-sizing: border-box; margin: 0; padding: 0; }
  html, body {
    width: 1200px; height: 1000px; overflow: hidden;
    background: var(--backdrop);
    font-family: "Jost", Arial, sans-serif;
  }
  .stage {
    position: relative; width: 1200px; height: 1000px;
  }
  .card {
    position: absolute; left: 250px;
    width: 700px; height: 400px;
    border-radius: 28px; overflow: hidden;
    background: var(--card-white);
    box-shadow: 0 14px 36px rgba(0,0,0,.45);
  }
  .card-front { top: 60px; }
  .card-back { top: 540px; }
  .card-art { position: absolute; inset: 0; width: 100%; height: 100%; }

  .brand {
    position: absolute; left: 300px; top: 120px; width: 320px;
    display: flex; align-items: center; gap: 14px;
  }
  .brand-dot {
    width: 46px; height: 46px; border-radius: 50%;
    background: var(--sun); flex: none;
  }
  .brand-name {
    font-weight: 700; font-size: 38px; line-height: 1.02;
    color: var(--cocoa);
  }

  .contact {
    position: absolute; left: 48px; top: 170px;
    color: var(--ink);
  }
  .contact-name {
    font-size: 30px; font-weight: 400; letter-spacing: 1px;
    text-transform: uppercase; color: var(--sun);
  }
  .contact-role { font-size: 13px; margin-top: 2px; }
  .contact-address { font-size: 15px; line-height: 1.35; margin-top: 18px; }
  .contact-lines { list-style: none; margin-top: 16px; font-size: 15px; line-height: 1.5; }
  .contact-lines li { display: flex; align-items: center; gap: 12px; }
  .contact-icon { width: 13px; height: 13px; flex: none; fill: var(--sun); }
  .web-accent { color: var(--sun); }
</style>
</head>
<body>
<main class="stage">

  <section class="card card-front" aria-label="Card front">
    <svg class="card-art" viewBox="0 0 700 400" aria-hidden="true">
      <rect width="700" height="400" fill="var(--cocoa)"/>
      <g transform="rotate(-10 420 150)">
        <ellipse cx="440" cy="120" rx="470" ry="250" fill="var(--card-white)"/>
        <ellipse cx="450" cy="115" rx="455" ry="240" fill="var(--sun)"/>
        <ellipse cx="490" cy="100" rx="420" ry="228" fill="var(--card-white)"/>
      </g>
    </svg>
    <div class="brand">
      <span class="brand-dot"></span>
      <span class="brand-name">Purrnest Nook Co</span>
    </div>
  </section>

  <section class="card card-back" aria-label="Card back">
    <svg class="card-art" viewBox="0 0 700 400" aria-hidden="true">
      <rect width="700" height="400" fill="var(--cocoa)"/>
      <g transform="rotate(-8 250 280)">
        <ellipse cx="230" cy="290" rx="450" ry="320" fill="var(--sun)"/>
        <ellipse cx="215" cy="310" rx="440" ry="305" fill="var(--card-white)"/>
        <ellipse cx="200" cy="320" rx="425" ry="298" fill="var(--cocoa)"/>
        <ellipse cx="185" cy="330" rx="415" ry="292" fill="var(--card-white)"/>
      </g>
    </svg>
    <div class="contact">
      <h1 class="contact-name">Lorna Kealoha</h1>
      <p class="contact-role">Director</p>
      <p class="contact-address">Your Street Address,<br>NewYork, 1234</p>
      <ul class="contact-lines">
        <li>
          <svg class="contact-icon" viewBox="0 0 16 16"><path d="M3.5 1l2.5 3-1.5 1.8c.9 2 2.6 3.7 4.7 4.7L11 9l3 2.5-1.3 2.6C7 14 2 9 1 3.3z"/></svg>
          <span>+1 (808) 571 6023</span>
        </li>
        <li>
          <svg class="contact-icon" viewBox="0 0 16 16"><path d="M1 3h14v10H1zM2 4l6 5 6-5" stroke="#fff" stroke-width="1"/></svg>
          <span>support@purrnestnookco.com</span>
        </li>
        <li>
          <svg class="contact-icon" viewBox="0 0 16 16"><circle cx="8" cy="8" r="7"/><path d="M1 8h14M8 1c3 3 3 11 0 14M8 1c-3 3-3 11 0 14" stroke="#fff" stroke-width="1" fill="none"/></svg>
          <span>www.<span class="web-accent">purrnestnookco</span>.com</span>
        </li>
      </ul>
    </div>
  </section>

</main>
</body>
</html>
```